Tallwick Home Services Web Site

Design Web site with 3-4 pages: Home, About Us, Services and Order form / Schedule Appointment (which will likely be link to Method App and Quickbooks integration.)
Services include: Dryer Vent Cleaning, AC Cleaning, Difficult-to-Reach Light Bulb replacement, Wood Repair and Home Maintenance Plans including Fire Safety Checks and Filter Replacement.

Target Market(s)

Luxury Home Owners, Professionals (Dr's/lawyers) and Seniors

Industry/Entity Type

Home Maintenance

Coding

Coded - Design and coding required

Requirements
Must have
• Tagline - Where Home Maintenance is Elementary

```html
<!DOCTYPE html>
<html lang="en">
<head>
<meta charset="utf-8">
<title>Tallwick Home Services</title>
<link href="https://fonts.googleapis.com/css2?family=Poppins:wght@400;500;600;700;800&display=swap" rel="stylesheet">
<style>
:root{
  --gold:#d89b1d;
  --gold-dark:#c48a14;
  --ink:#333436;
  --text:#444;
  --muted:#666;
  --paper:#ffffff;
  --mist:#efefef;
  --night:#252525;
  --black:#0b0b0b;
  --field:#2e2e2e;
}
*{box-sizing:border-box;margin:0;padding:0}
html,body{width:1200px;height:5076px;overflow:hidden}
body{position:relative;font-family:"Poppins",sans-serif;color:var(--text);background:var(--paper)}
h2,h3,h4{font-weight:inherit}
.abs{position:absolute}
a{color:inherit;text-decoration:none}

/* header */
.brand{left:72px;top:14px;width:176px;height:132px;background:var(--paper);display:flex;flex-direction:column;align-items:center;justify-content:center;z-index:3}
.brand .dot{width:34px;height:34px;border-radius:50%;background:var(--gold);margin-bottom:8px}
.brand .name{font-weight:700;font-size:24px;color:var(--gold);letter-spacing:1px;line-height:1}
.brand .sub{font-size:10px;color:var(--ink);letter-spacing:1px;margin-top:4px}
.topbar{right:74px;top:18px;display:flex;align-items:center;gap:18px}
.topbar .phone{display:flex;align-items:center;gap:8px;color:var(--gold);font-weight:500;font-size:16px}
.topbar .phone i{width:28px;height:28px;border-radius:50%;background:var(--ink);display:flex;align-items:center;justify-content:center}
.btn{display:inline-flex;align-items:center;justify-content:center;background:var(--gold);color:#fff;font-weight:700;border-radius:30px;letter-spacing:.5px}
.topbar .btn{height:42px;padding:0 24px;font-size:13px}
.nav{right:74px;top:76px;display:flex;gap:40px;font-size:13px;font-weight:600;color:var(--ink)}
.nav a.on{color:var(--gold);position:relative}
.nav a.on::after{content:"";position:absolute;left:-8px;right:-8px;top:24px;height:6px;background:var(--gold)}

/* hero */
.hero{left:0;top:110px;width:1200px;height:590px;background:linear-gradient(90deg,#d9d9d9 0%,#bdbdbd 45%,#8e8e8e 70%,#6e6e6e 100%)}
.hero-title{left:72px;top:248px}
.hero-title .a{font-size:74px;font-weight:700;color:var(--gold);line-height:1}
.hero-title .b{font-size:56px;font-weight:400;color:var(--ink);line-height:1.1;letter-spacing:1px}
.hero-sub{left:74px;top:388px;width:530px;font-size:19px;font-weight:600;color:var(--black);line-height:1.55}
.hero-btn{left:74px;top:480px;width:214px;height:52px;font-size:16px}
.dots{left:74px;top:631px;display:flex;gap:9px}
.dots i{width:10px;height:10px;border-radius:50%;background:#fff}
.dots i:first-child{background:var(--ink)}

/* welcome */
.emblem{left:56px;top:820px;width:534px;height:320px;display:flex;align-items:center;justify-content:center;gap:24px}
.emblem .dot{width:120px;height:120px;border-radius:50%;background:var(--ink)}
.emblem .name{font-size:70px;font-weight:700;color:var(--gold)}
.eyebrow{font-size:35px;font-weight:400;color:var(--ink);line-height:1.15;letter-spacing:1px}
.eyebrow b{display:block;color:var(--gold);font-weight:700}
.welcome-head{left:616px;top:796px}
.welcome-copy{left:616px;top:896px;width:512px;font-size:14px;line-height:2.05;color:var(--text)}
.welcome-btn{left:616px;top:1152px;width:198px;height:50px;font-size:16px}

.band{left:0;width:1200px}
.section-head{left:0;width:1200px;text-align:center;font-size:36px;font-weight:400;color:var(--ink);letter-spacing:1px}
.section-head b{color:var(--gold);font-weight:700}
.mini-dot{width:26px;height:26px;border-radius:50%;background:var(--gold);left:587px}

/* services */
.card{width:329px;background:#fff;border-radius:12px;overflow:hidden;box-shadow:0 2px 10px rgba(0,0,0,.08);text-align:center}
.card .ph{height:235px}
.card h3{font-size:23px;font-weight:700;color:var(--gold);line-height:1.25;margin:20px 20px 10px}
.card p{font-size:13.5px;line-height:1.85;color:var(--text);padding:0 22px}
.card.hot{background:var(--gold)}
.card.hot h3,.card.hot p{color:#fff}
.all-btn{left:477px;top:2610px;width:246px;height:52px;font-size:16px}

/* testimonials */
.quote{width:500px;display:flex;gap:26px}
.quote .pic{flex:none;width:152px;height:152px;border-radius:50%;position:relative}
.quote .pic::after{content:"";position:absolute;right:-10px;bottom:-2px;width:52px;height:42px;border-radius:50% 50% 10px 50%;background:var(--gold)}
.quote p{font-size:14px;line-height:1.75;color:var(--text)}
.quote h4{font-size:15px;font-weight:600;color:var(--gold);margin-top:10px}
.arrows{left:570px;top:3160px;display:flex;gap:16px}

/* why */
.why-head{left:78px;top:3418px}
.why-head.eyebrow{color:var(--ink)}
.why-head.eyebrow b{color:#fff}
.why-copy{left:78px;top:3518px;width:490px;font-size:14px;line-height:2.05;color:#fff}
.why-btn{left:78px;top:3658px;width:198px;height:50px;font-size:16px;background:var(--ink)}
.why-photo{left:617px;top:3384px;width:583px;height:362px;border-radius:180px 0 0 180px;background:linear-gradient(120deg,#e9e9e9,#b9c2cc 55%,#3a3f4a)}

/* blog */
.post{width:330px}
.post .ph{height:205px;border-radius:12px}
.post h3{font-size:23px;font-weight:700;color:var(--ink);line-height:1.35;margin-top:22px}
.post p{font-size:14px;line-height:1.9;color:var(--text);margin-top:8px}
.post .more{display:block;font-size:14px;font-weight:600;color:var(--gold);margin-top:16px}

/* footer */
.f-brand{left:84px;top:4690px;width:170px;text-align:center}
.f-brand .dot{width:46px;height:46px;border-radius:50%;background:var(--gold);margin:0 auto 12px}
.f-brand .name{font-size:28px;font-weight:700;color:var(--gold);letter-spacing:1px}
.f-brand .sub{font-size:12px;color:#999;letter-spacing:1px}
.f-copy{left:60px;top:4850px;width:210px;text-align:center;font-size:11px;line-height:2.1;color:#ddd}
.f-title{font-size:14px;font-weight:700;color:var(--gold);letter-spacing:.5px}
.f-links{left:352px;top:4676px}
.f-links ul{list-style:none;margin-top:14px}
.f-links li{font-size:13px;color:#eee;line-height:2.5}
.f-contact{left:538px;top:4676px;width:240px}
.f-contact .row{display:flex;gap:10px;font-size:13px;color:#eee;line-height:1.8;margin-top:10px}
.f-contact .row svg{flex:none;margin-top:5px}
.f-contact .row.gold{color:var(--gold);font-weight:600}
.social{left:538px;top:4890px;display:flex;gap:14px}
.social i{display:block;width:22px;height:22px;border-radius:50%;background:#fff}
.appt{left:793px;top:4520px;width:335px;height:500px;background:var(--black);padding:30px 24px}
.appt .eyebrow{font-size:34px;color:#fff}
.appt .eyebrow b{color:var(--gold)}
.field{height:44px;border-radius:22px;background:var(--field);font-size:12px;color:#ddd;padding:0 18px;display:flex;align-items:center;margin-top:14px}
.field.big{height:104px;border-radius:16px;align-items:flex-start;padding-top:12px}
.appt .btn{width:100%;height:44px;font-size:16px;margin-top:22px}
</style>
</head>
<body>

<!-- header -->
<div class="abs brand"><div class="dot"></div><div class="name">TALLWICK</div><div class="sub">— HOME SERVICES —</div></div>
<div class="abs topbar">
  <span class="phone"><i><svg width="14" height="14" viewBox="0 0 24 24"><path fill="#fff" d="M6.6 10.8a15 15 0 0 0 6.6 6.6l2.2-2.2c.3-.3.7-.4 1-.2 1.1.4 2.3.6 3.6.6.6 0 1 .4 1 1V20c0 .6-.4 1-1 1A17 17 0 0 1 3 4c0-.6.4-1 1-1h3.5c.6 0 1 .4 1 1 0 1.3.2 2.5.6 3.6.1.3 0 .7-.2 1z"/></svg></i>+1-555-014-2290</span>
  <a class="btn" href="#">SCHEDULE APPOINTMENT</a>
</div>
<nav class="abs nav"><a class="on" href="#">HOME</a><a href="#">ABOUT US</a><a href="#">SERVICES</a><a href="#">TESTIMONIALS</a><a href="#">BLOG</a><a href="#">CONTACT US</a></nav>

<!-- hero -->
<div class="abs hero" role="img" aria-label="Technician with flashlight and safety glasses looking through a dryer vent duct"></div>
<div class="abs hero-title"><div class="a">Tallwick</div><div class="b">Homes Services</div></div>
<p class="abs hero-sub">Where Home Maintenance is Elementary.<br>Trusted care for every corner of your home.</p>
<a class="abs btn hero-btn" href="#">CONTACT US</a>
<div class="abs dots"><i></i><i></i><i></i><i></i></div>

<!-- welcome -->
<div class="abs emblem"><div class="dot"></div><div class="name">Tallwick</div></div>
<h2 class="abs eyebrow welcome-head">WELCOME TO<b>TALLWICK HOMES</b></h2>
<p class="abs welcome-copy">Sed ut perspiciatis unde omnis iste natus error sit voluptatem accusantium doloremque laudantium, totam rem aperiam, eaque ipsa quae ab illo inventore veritatis et quasi architecto beatae vitae dicta sunt explicabo. Nemo enim ipsam voluptatem quia voluptas sit aspernatur aut odit aut fugit, sed quia consequuntur magni dolores eos qui ratione voluptatem sequi nesciunt. Neque porro quisquam est, qui dolorem ipsum quia dolor sit amet, consectetur, adipisci velit..</p>
<a class="abs btn welcome-btn" href="#">READ MORE</a>

<!-- services band -->
<svg class="abs band" style="top:1240px" width="1200" height="1560" viewBox="0 0 1200 1560" preserveAspectRatio="none">
  <path fill="#efefef" d="M0 20 C200 -20 380 120 600 120 C820 120 960 20 1200 40 V1500 C1000 1420 850 1470 600 1480 C380 1490 200 1430 0 1450 Z"/>
</svg>
<div class="abs mini-dot" style="top:1412px"></div>
<h2 class="abs section-head" style="top:1456px">OUR <b>SERVICES</b></h2>

<div class="abs card" style="left:75px;top:1550px;height:435px"><div class="ph" style="background:linear-gradient(160deg,#cfcfcf,#8a8a8a)" role="img" aria-label="Technician cleaning a dryer vent behind a washing machine"></div><h3>Dryer Vent<br>Cleaning</h3><p>Nemo enim ipsam voluptatem quia voluptas sit aspernatur aut odit aut fugit culpa qui officia deserunt mollit.</p></div>
<div class="abs card hot" style="left:434px;top:1550px;height:530px"><div class="ph" style="background:linear-gradient(160deg,#e9dcc4,#6b5a46)" role="img" aria-label="Hands replacing a ceiling light bulb"></div><h3>Light Bulb<br>Replacement</h3><p>Nemo enim ipsam voluptatem quia voluptas sit aspernatur aut odit aut fugit culpa qui officia deserunt mollit. aute irure dolor in reprehenderit in voluptate velit esse cillum dolore eu fugiat nulla pariatur.</p></div>
<div class="abs card" style="left:797px;top:1550px;height:435px"><div class="ph" style="background:linear-gradient(160deg,#e4e8ec,#5d6c80)" role="img" aria-label="Gloved hands servicing a wall air conditioner"></div><h3>AC<br>Cleaning</h3><p>Nemo enim ipsam voluptatem quia voluptas sit aspernatur aut odit aut fugit culpa qui officia deserunt mollit.</p></div>

<div class="abs card" style="left:75px;top:2015px;height:530px"><div class="ph" style="background:linear-gradient(160deg,#d8c3a4,#4a3e33)" role="img" aria-label="Carpenter repairing a kitchen countertop"></div><h3>Wood Repair and Home<br>Maintenance Plans</h3><p>Nemo enim ipsam voluptatem quia voluptas sit aspernatur aut odit aut fugit culpa qui officia deserunt mollit. aute irure dolor in reprehenderit in voluptate velit esse cillum dolore eu fugiat nulla pariatur.</p></div>
<div class="abs card" style="left:434px;top:2110px;height:435px"><div class="ph" style="background:linear-gradient(160deg,#ededed,#8d6a4a)" role="img" aria-label="Worker in hard hat checking a ceiling smoke detector"></div><h3>Fire Safety<br>Checks</h3><p>Nemo enim ipsam voluptatem quia voluptas sit aspernatur aut odit aut fugit culpa qui officia deserunt mollit.</p></div>
<div class="abs card" style="left:797px;top:2015px;height:530px"><div class="ph" style="background:linear-gradient(160deg,#eef0f1,#9aa3a8)" role="img" aria-label="Couple replacing an air conditioner filter"></div><h3>Filter<br>Replacement</h3><p>Nemo enim ipsam voluptatem quia voluptas sit aspernatur aut odit aut fugit culpa qui officia deserunt mollit. aute irure dolor in reprehenderit in voluptate velit esse cillum dolore eu fugiat nulla pariatur.</p></div>

<a class="abs btn all-btn" href="#">VIEW ALL SERVICES</a>

<!-- testimonials -->
<div class="abs mini-dot" style="top:2830px"></div>
<h2 class="abs section-head" style="top:2874px">CLIENT <b>TESTIMONIALS</b></h2>
<div class="abs quote" style="left:75px;top:2960px"><div class="pic" style="background:linear-gradient(160deg,#b7c7a6,#5d6b4a)" role="img" aria-label="Portrait of a smiling client"></div><div><p>“ Sed ut perspiciatis unde omnis iste natus error sit voluptatem accusantium doloremque laudantium, totam rem aperiam, eaque ipsa quae ab illo inventore veritatis et quasi architecto..”</p><h4>Name Heading</h4></div></div>
<div class="abs quote" style="left:618px;top:2960px"><div class="pic" style="background:linear-gradient(160deg,#d9d2c4,#6f7a8a)" role="img" aria-label="Portrait of a senior client"></div><div><p>“ Sed ut perspiciatis unde omnis iste natus error sit voluptatem accusantium doloremque laudantium, totam rem aperiam, eaque ipsa quae ab illo inventore veritatis et quasi architecto..”</p><h4>Name Heading</h4></div></div>
<div class="abs arrows">
  <svg width="26" height="22" viewBox="0 0 26 22"><path d="M24 11H4M11 3 3 11l8 8" stroke="#333" stroke-width="4" fill="none"/></svg>
  <svg width="26" height="22" viewBox="0 0 26 22"><path d="M2 11h20M15 3l8 8-8 8" stroke="#d89b1d" stroke-width="4" fill="none"/></svg>
</div>

<!-- why choose -->
<svg class="abs band" style="top:3170px" width="1200" height="660" viewBox="0 0 1200 660" preserveAspectRatio="none">
  <path fill="#d89b1d" d="M0 40 C220 120 420 40 640 60 C860 80 1000 150 1200 110 V660 H0 Z"/>
</svg>
<h2 class="abs eyebrow why-head">WHY CHOOSE<b>TALLWICK HOMES</b></h2>
<p class="abs why-copy">Sed ut perspiciatis unde omnis iste natus error sit voluptatem accusantium doloremque laudantium, totam rem aperiam, eaque ipsa quae ab illo inventore veritatis et quasi architecto beatae occaecat cupidatat non proident.</p>
<a class="abs btn why-btn" href="#">READ MORE</a>
<div class="abs why-photo" role="img" aria-label="Smiling technician in cap servicing an air conditioner unit"></div>

<!-- blog -->
<div class="abs mini-dot" style="top:3895px"></div>
<h2 class="abs section-head" style="top:3938px">LATEST <b>BLOG</b></h2>
<div class="abs post" style="left:75px;top:4010px"><div class="ph" style="background:linear-gradient(160deg,#f0f0f0,#a7a29c)" role="img" aria-label="Technician opening an indoor air conditioner"></div><h3>Sed ut perspiciatis unde omnis iste</h3><p>Nemo enim ipsam voluptatem quia voluptas sit aspernatur aut odit aut fugit, sed quia consequuntur magni..</p><a class="more" href="#">Read More</a></div>
<div class="abs post" style="left:436px;top:4010px"><div class="ph" style="background:linear-gradient(160deg,#ece7df,#6c5d4f)" role="img" aria-label="Man changing a pendant light bulb"></div><h3>Sed ut perspiciatis unde omnis iste</h3><p>Nemo enim ipsam voluptatem quia voluptas sit aspernatur aut odit aut fugit, sed quia consequuntur magni..</p><a class="more" href="#">Read More</a></div>
<div class="abs post" style="left:797px;top:4010px"><div class="ph" style="background:linear-gradient(160deg,#4b5a72,#b52a24)" role="img" aria-label="Inspector checking fire extinguishers"></div><h3>Sed ut perspiciatis unde omnis iste</h3><p>Nemo enim ipsam voluptatem quia voluptas sit aspernatur aut odit aut fugit, sed quia consequuntur magni..</p><a class="more" href="#">Read More</a></div>
<svg class="abs" style="left:1140px;top:4170px" width="32" height="32" viewBox="0 0 32 32"><circle cx="16" cy="16" r="15" fill="#333"/><path d="M23 16H10m5-6-6 6 6 6" stroke="#fff" stroke-width="3" fill="none"/></svg>
<svg class="abs" style="left:1140px;top:4216px" width="32" height="32" viewBox="0 0 32 32"><circle cx="16" cy="16" r="15" fill="#d89b1d"/><path d="M9 16h13m-5-6 6 6-6 6" stroke="#fff" stroke-width="3" fill="none"/></svg>

<!-- footer -->
<svg class="abs band" style="top:4490px" width="1200" height="586" viewBox="0 0 1200 586" preserveAspectRatio="none">
  <path fill="#252525" d="M0 0 C160 60 360 70 600 60 C840 50 1000 40 1200 70 V586 H0 Z"/>
</svg>
<div class="abs f-brand"><div class="dot"></div><div class="name">TALLWICK</div><div class="sub">— HOME SERVICES —</div></div>
<p class="abs f-copy">Copyright © 2025 Company Name<br>All Right Reserved</p>
<div class="abs f-links"><div class="f-title">QUICK LINKS</div><ul><li>Home</li><li>About Us</li><li>Services</li><li>Testimonials</li><li>Blog</li><li>Contact Us</li></ul></div>
<div class="abs f-contact"><div class="f-title">CONTACT INFO</div>
  <div class="row"><svg width="12" height="12" viewBox="0 0 12 12"><rect width="12" height="10" fill="#d89b1d"/></svg><span>48 Larkspur Lane Suite 12,<br>Brookvale 20417, United States</span></div>
  <div class="row"><svg width="12" height="12" viewBox="0 0 24 24"><path fill="#d89b1d" d="M6.6 10.8a15 15 0 0 0 6.6 6.6l2.2-2.2c.3-.3.7-.4 1-.2 1.1.4 2.3.6 3.6.6.6 0 1 .4 1 1V20c0 .6-.4 1-1 1A17 17 0 0 1 3 4c0-.6.4-1 1-1h3.5c.6 0 1 .4 1 1 0 1.3.2 2.5.6 3.6.1.3 0 .7-.2 1z"/></svg><span>+1-555-014-2290</span></div>
  <div class="row"><svg width="12" height="10" viewBox="0 0 12 10"><rect width="12" height="10" fill="#d89b1d"/><path d="M0 0l6 5 6-5" stroke="#252525" fill="none"/></svg><span>hello@tallwickhome.com</span></div>
  <div class="row gold"><svg width="12" height="14" viewBox="0 0 12 14"><path fill="#d89b1d" d="M6 0a6 6 0 0 1 6 6c0 4-6 8-6 8S0 10 0 6a6 6 0 0 1 6-6z"/><circle cx="6" cy="6" r="2" fill="#252525"/></svg><span>Map Direction</span></div>
</div>
<div class="abs social" aria-label="Social media links">
  <a href="#" aria-label="Social link 1"><i></i></a>
  <a href="#" aria-label="Social link 2"><i></i></a>
  <a href="#" aria-label="Social link 3"><i></i></a>
  <a href="#" aria-label="Social link 4"><i></i></a>
  <a href="#" aria-label="Social link 5"><i></i></a>
</div>
<div class="abs appt">
  <h2 class="eyebrow">SCHEDULE<b>APPOINTMENT</b></h2>
  <div style="margin-top:14px">
    <div class="field">Name</div>
    <div class="field">Email Address</div>
    <div class="field">Phone No</div>
    <div class="field big">Message</div>
    <a class="btn" href="#">SUBMIT</a>
  </div>
</div>

</body>
</html>
```